Business Card Design (NEW FILES)

ATTENTION: New vector files are available. Please update your design to reflect/use the new (better resolution) logo images.

Seeking a unique and professional business card design for a commercial drone photography/videography business. The layout should feature
the logo (attached) and include the following information:
Owen Tarrick
614-502-7738
www.skylarkreelworks.example
NRD Certified Remote Pilot

Owen Tarrick

```html
<!DOCTYPE html>
<html lang="en">
<head>
<meta charset="utf-8">
<title>Skylark Reelworks – Business Card</title>
<link href="https://fonts.googleapis.com/css2?family=Montserrat:wght@500;700&family=Open+Sans:wght@400;600&display=swap" rel="stylesheet">
<style>
  :root {
    --stage: #222222;
    --paper: #ffffff;
    --navy: #1b1f5c;
    --navy-deep: #141845;
    --orange: #ec8a4c;
    --ink: #1b1f5c;
    --ghost: #ecebf0;
  }
  * { margin: 0; padding: 0; box-sizing: border-box; }
  html, body { width: 1200px; height: 780px; overflow: hidden; }
  body {
    background: var(--stage);
    font-family: "Open Sans", Arial, sans-serif;
    display: flex;
    align-items: center;
    justify-content: center;
    gap: 40px;
  }
  .card {
    position: relative;
    width: 540px;
    height: 310px;
    overflow: hidden;
  }
  /* Front */
  .card-front { background: var(--paper); color: var(--ink); }
  .swoosh { position: absolute; inset: 0; width: 100%; height: 100%; }
  .brand {
    position: absolute;
    top: 26px; left: 30px;
    display: flex; align-items: center; gap: 10px;
  }
  .brand-dot { width: 14px; height: 14px; border-radius: 50%; background: var(--orange); }
  .brand-name {
    font-family: "Montserrat", Arial, sans-serif;
    font-weight: 500;
    font-size: 26px;
    letter-spacing: 1px;
    color: var(--navy);
    text-transform: uppercase;
  }
  .credentials {
    position: absolute;
    top: 92px; left: 30px;
    font-size: 13px;
    line-height: 20px;
  }
  .contact {
    position: absolute;
    top: 138px; left: 30px;
    list-style: none;
    font-size: 13px;
    line-height: 20px;
  }
  .contact li { display: flex; align-items: center; gap: 8px; }
  .contact svg { width: 11px; height: 11px; flex: none; }
  .decor-ghost {
    position: absolute;
    right: 70px; top: 110px;
    width: 170px; height: 130px;
    border-radius: 40px;
    background: radial-gradient(ellipse at center, var(--ghost) 0%, rgba(236,235,240,0) 70%);
  }
  .holder {
    position: absolute;
    right: 46px; bottom: 48px;
    text-align: right;
  }
  .holder-name {
    font-family: "Montserrat", Arial, sans-serif;
    font-weight: 700;
    font-size: 27px;
    line-height: 1.1;
  }
  .holder-name .first { color: var(--orange); }
  .holder-name .last { color: var(--navy); }
  .holder-role { font-size: 14px; margin-top: 2px; color: var(--navy); }
  .corner-tab {
    position: absolute;
    right: 0; bottom: 0;
    width: 30px; height: 46px;
    background: var(--orange);
  }
  /* Back */
  .card-back { background: var(--navy-deep); }
  .pattern {
    position: absolute; inset: 0;
    background: linear-gradient(160deg, #151a4e 0%, #1d2466 55%, #243089 100%);
  }
  .back-brand {
    position: absolute;
    left: 50%; top: 50%;
    transform: translate(-50%, -50%);
    display: flex; align-items: center; gap: 8px;
  }
  .back-brand .brand-name { color: var(--paper); font-size: 20px; }
</style>
</head>
<body>

<section class="card card-front" aria-label="Business card front">
  <svg class="swoosh" viewBox="0 0 540 310" preserveAspectRatio="none" aria-hidden="true">
    <path d="M0,172 C120,222 250,250 318,310 L302,310 C240,262 115,236 0,192 Z" fill="var(--orange)"/>
    <path d="M0,200 C115,244 238,270 296,310 L0,310 Z" fill="var(--navy)"/>
  </svg>

  <div class="brand">
    <span class="brand-dot"></span>
    <span class="brand-name">Skylark Reelworks</span>
  </div>

  <p class="credentials">NRD Certified Remote Pilot<br>Fully Insured</p>

  <ul class="contact">
    <li>
      <svg viewBox="0 0 12 12" aria-hidden="true"><path d="M2.5 1 L4.5 1 L5.2 3.6 L4 4.6 C4.7 6.1 5.9 7.3 7.4 8 L8.4 6.8 L11 7.5 L11 9.5 C11 10.3 10.3 11 9.5 11 C5 11 1 7 1 2.5 C1 1.7 1.7 1 2.5 1 Z" fill="var(--orange)"/></svg>
      614-502-7738
    </li>
    <li>
      <svg viewBox="0 0 12 12" aria-hidden="true"><circle cx="6" cy="6" r="5" fill="none" stroke="var(--orange)" stroke-width="1.4"/><path d="M1 6 H11 M6 1 C3.5 4 3.5 8 6 11 M6 1 C8.5 4 8.5 8 6 11" fill="none" stroke="var(--orange)" stroke-width="1"/></svg>
      www.skylarkreelworks.example
    </li>
  </ul>

  <div class="decor-ghost" role="img" aria-label="Faint drone decoration in pale grey"></div>

  <div class="holder">
    <p class="holder-name"><span class="first">Owen</span> <span class="last">Tarrick</span></p>
    <p class="holder-role">Owner</p>
  </div>

  <div class="corner-tab"></div>
</section>

<section class="card card-back" aria-label="Business card back">
  <div class="pattern" role="img" aria-label="Repeating drone pattern in shades of navy blue"></div>
  <div class="back-brand">
    <span class="brand-dot"></span>
    <span class="brand-name">Skylark Reelworks</span>
  </div>
</section>

</body>
</html>
```